Professional Single Page Website Design for Tollbrook Advisory

Tollbrook Advisory is a new business consultancy specializing in providing expert services to small businesses, primarily in the brick-and-mortar retail and food service sectors. We offer a range of services including franchise development and launch, due diligence, and construction management.

Currently, we have a basic website set up at www.tollbrookadvisory.example, but we need a professional touch to enhance its design and functionality.

Project Requirements:
- Single Page Design: For now, we need a single page design that effectively showcases who we are, our services, and contact information.
- Future Expansion: The design should be flexible and scalable for future expansion to include additional pages like specific service offerings, about us, and a dedicated contact page.
- Design Aesthetic: We are looking for a modern yet professional design that aligns with our brand identity.
- Logo: We have a logo that we like, which was also sourced from Pixel Bazaar. The logo files are attached to this project brief.

Key Sections to Include:
- Hero Section: An engaging introduction to Tollbrook Advisory with a strong visual impact.
- About Us: A brief overview of who we are and our mission.
- Team: Section for the profiles of the two principals.
- Services: A clear and concise presentation of our services, including franchise development, due diligence, and construction management.
- Contact Information: Easy-to-find contact details, including a form for inquiries.
- Call to Action: Encouraging visitors to get in touch with us for consultations or further information.

Design Considerations:
- Ensure the design is responsive and mobile-friendly.
- Include high-quality images and icons that complement our services and industry.
- We do not need development services, this is only a design project.

```html
<!DOCTYPE html>
<html lang="en">
<head>
<meta charset="utf-8">
<title>Tollbrook Advisory</title>
<link href="https://fonts.googleapis.com/css2?family=Poppins:wght@600;700&family=Roboto:wght@400;500;700&display=swap" rel="stylesheet">
<style>
:root{
  --green:#8dc4a7;
  --green-band:#94c6ac;
  --mint:#e9f8f1;
  --ink:#1f1f1f;
  --text:#4a4a4a;
  --muted:#6b6b6b;
  --forest:#1c3b2b;
  --white:#ffffff;
}
*{box-sizing:border-box;margin:0;padding:0}
html,body{width:1200px;height:3266px;overflow:hidden}
body{font-family:'Roboto',Arial,sans-serif;color:var(--text);background:var(--white);position:relative}
h1,h2,h3{font-family:'Poppins',Arial,sans-serif;font-weight:700;color:var(--ink)}
.btn{display:inline-flex;align-items:center;gap:8px;background:var(--green);color:var(--white);font:500 15px 'Roboto',sans-serif;text-transform:uppercase;padding:0 16px;border:none;height:38px}
.btn svg{width:14px;height:14px}

/* header */
.site-header{height:91px;display:flex;align-items:center;padding:0 113px;justify-content:space-between}
.brand{display:flex;align-items:center;gap:12px;font:700 22px 'Poppins',sans-serif;color:#2d6b55}
.brand-dot{width:44px;height:44px;border-radius:50%;border:5px solid var(--green)}
.main-nav{display:flex;align-items:center;gap:30px;font-size:15px;color:#333;margin-left:auto;margin-right:32px}
.main-nav .sep{color:#555}
.site-header .btn{height:46px;padding:0 30px}

/* hero */
.hero{position:relative;height:643px;background:linear-gradient(120deg,#9fb8c9 0%,#7a8a8c 25%,#8a4a3a 50%,#6d3b30 70%,#3a3f44 100%)}
.hero-box{position:absolute;left:237px;top:246px;width:726px;padding:28px 20px 22px;background:rgba(40,40,40,.55);text-align:center;color:var(--white)}
.hero-box h1{color:var(--white);font-size:38px;line-height:48px}
.hero-box h2{color:var(--white);font-size:21px;margin:12px 0 14px}
.hero-box p{font-size:12px;line-height:26px}
.hero-box .btn{margin-top:14px;height:44px}

/* mission */
.mission{height:244px;background:var(--green-band);text-align:center;padding-top:52px}
.mission h2{color:var(--white);font-size:38px}
.mission p{color:var(--white);font-size:15px;line-height:26px;width:830px;margin:12px auto 0}

/* services */
.services{height:707px;position:relative;text-align:center}
.services h2{font-size:38px;padding-top:78px}
.service-card{position:absolute;top:1138px;width:308px;height:461px;background:var(--white);box-shadow:0 2px 12px rgba(0,0,0,.16);padding:8px;text-align:center}
.service-photo{height:214px}
.service-card h3{font:500 17px/26px 'Roboto',sans-serif;color:var(--ink);margin-top:28px}
.service-card p{font-size:14px;line-height:22px;color:var(--muted);margin-top:8px;padding:0 4px}
.service-card .btn{margin-top:22px}
.arrow{position:absolute;top:1345px;width:46px;height:46px;border:2px solid #222;border-radius:50%;display:flex;align-items:center;justify-content:center}

/* who */
.who{height:552px;background:var(--mint);position:relative}
.who-photo{position:absolute;left:127px;top:70px;width:418px;height:418px;border-radius:50%;border:14px solid #b7ccc0;background:linear-gradient(135deg,#e8e2d6,#b9553f 55%,#2f3d3c)}
.who-text{position:absolute;left:604px;top:76px;width:469px}
.who-text h2{font-size:38px}
.who-text p{font-size:15.5px;line-height:26.6px;text-align:justify;margin-top:8px}
.who-text .btn{margin-top:24px;height:46px;padding:0 20px}

/* team */
.team{height:544px;text-align:center;position:relative}
.team h2{font-size:38px;padding-top:78px}
.team-card{position:absolute;top:160px;width:477px;height:283px;background:var(--white);box-shadow:0 2px 14px rgba(0,0,0,.12);padding:30px 26px;text-align:left}
.member{display:flex;align-items:center;gap:14px}
.avatar{width:78px;height:78px;border-radius:50%;border:3px solid var(--green);background:linear-gradient(#c9d4da,#6c7a85)}
.member h3{font-size:19px}
.member span{color:var(--green);font:600 15px 'Poppins',sans-serif}
.team-card p{font-size:14.5px;line-height:25.6px;text-align:justify;margin-top:22px}
.team-card a{color:var(--green);text-decoration:none}

/* footer */
.site-footer{height:485px;background:var(--forest);position:relative;color:var(--white)}
.site-footer h4{font:500 18px 'Roboto',sans-serif;text-transform:uppercase;position:absolute}
.field{position:absolute;background:var(--white);color:#666;font-size:12px;padding:14px 18px}
.quick{position:absolute;left:633px;top:122px;list-style:none;font-size:14.5px;line-height:30px}
.quick li::before{content:"»";margin-right:12px}
.contact{position:absolute;left:864px;top:126px;list-style:none;font-size:14.5px}
.contact li{display:flex;gap:14px;margin-bottom:14px;line-height:24px}
.contact svg{width:14px;height:14px;flex:none;margin-top:5px}
.socials{position:absolute;left:833px;top:290px;display:flex;gap:7px}
.socials span{width:33px;height:33px;border-radius:50%;background:var(--white)}
.footer-bottom{position:absolute;left:103px;right:118px;top:414px;border-top:1px solid rgba(255,255,255,.35);text-align:center;padding-top:34px;font-size:14px}
</style>
</head>
<body>

<header class="site-header">
  <div class="brand"><span class="brand-dot"></span>Tollbrook Advisory</div>
  <nav class="main-nav">
    <span>Home</span><span class="sep">/</span><span>About Us</span><span class="sep">/</span><span>Team</span><span class="sep">/</span><span>Services</span><span class="sep">/</span><span>Contact Us</span>
  </nav>
  <a class="btn">Login <svg viewBox="0 0 16 16"><circle cx="8" cy="8" r="8" fill="#fff"/><path d="M6 4l4 4-4 4" stroke="#8dc4a7" stroke-width="2" fill="none"/></svg></a>
</header>

<section class="hero" role="img" aria-label="Photo of a modern brick retail storefront with an empty parking lot">
  <div class="hero-box">
    <h1>Building Success in Southern California</h1>
    <h2>Expertise at Every Step: From Planning to Execution</h2>
    <p>At Tollbrook, we blend innovative strategies with local market expertise to guide your commercial real estate ventures. Whether you're launching a new restaurant, investing in retail spaces, or expanding a franchise, our dedicated team is here to turn your real estate aspirations into tangible success. Dive into a partnership that grows with you.</p>
    <a class="btn">Get in touch <svg viewBox="0 0 16 16"><circle cx="8" cy="8" r="8" fill="#fff"/><path d="M6 4l4 4-4 4" stroke="#8dc4a7" stroke-width="2" fill="none"/></svg></a>
  </div>
</section>

<section class="mission">
  <h2>Our Mission</h2>
  <p>Lorem ipsum dolor sit amet, consectetur adipiscing elit, sed do eiusmod tempor incididunt ut labore et dolore magna aliqua. Ut enim ad minim veniam, quis nostrud exercitation ullamco laboris nisi ut aliquip ex ea commodo consequat. Duis aute irure dolor in reprehenderit in voluptate velit esse cillum</p>
</section>

<section class="services">
  <h2>Our Services</h2>
</section>
<div class="arrow" style="left:32px"><svg width="16" height="16" viewBox="0 0 16 16"><path d="M11 2L5 8l6 6" stroke="#222" stroke-width="2" fill="none"/></svg></div>
<div class="arrow" style="left:1121px"><svg width="16" height="16" viewBox="0 0 16 16"><path d="M5 2l6 6-6 6" stroke="#222" stroke-width="2" fill="none"/></svg></div>

<article class="service-card" style="left:125px">
  <div class="service-photo" role="img" aria-label="Photo of consultants meeting with a client at a table" style="background:linear-gradient(135deg,#d9d4cc,#8a6a52 60%,#3b3a3c)"></div>
  <h3>Franchise Development &amp;<br>Launch</h3>
  <p>At Tollbrook Advisory, our Franchise Development &amp; Launch service is designed to transform your successful business.</p>
  <a class="btn">Learn more <svg viewBox="0 0 16 16"><circle cx="8" cy="8" r="8" fill="#fff"/><path d="M6 4l4 4-4 4" stroke="#8dc4a7" stroke-width="2" fill="none"/></svg></a>
</article>
<article class="service-card" style="left:452px">
  <div class="service-photo" role="img" aria-label="Photo of a presenter leading a team discussion in an office" style="background:linear-gradient(135deg,#cfd6d8,#8b8a6e 55%,#3d4a5a)"></div>
  <h3>Due Diligence Services</h3>
  <p>Tollbrook offers comprehensive evaluations tailored to your business needs. We meticulously assess franchise opportunities, business sales,</p>
  <a class="btn">Learn more <svg viewBox="0 0 16 16"><circle cx="8" cy="8" r="8" fill="#fff"/><path d="M6 4l4 4-4 4" stroke="#8dc4a7" stroke-width="2" fill="none"/></svg></a>
</article>
<article class="service-card" style="left:780px">
  <div class="service-photo" role="img" aria-label="Photo of colleagues reviewing plans at a laptop" style="background:linear-gradient(135deg,#e4e6e2,#9aa3a6 55%,#3f4f60)"></div>
  <h3>Building &amp; Construction<br>Management</h3>
  <p>Our Building &amp; Construction Management Services oversee every aspect of your construction and development projects,</p>
  <a class="btn">Learn more <svg viewBox="0 0 16 16"><circle cx="8" cy="8" r="8" fill="#fff"/><path d="M6 4l4 4-4 4" stroke="#8dc4a7" stroke-width="2" fill="none"/></svg></a>
</article>

<section class="who">
  <div class="who-photo" role="img" aria-label="Photo of a smiling woman in a red jacket talking with a colleague"></div>
  <div class="who-text">
    <h2>Who We Are</h2>
    <p>Welcome to Tollbrook Advisory, your trusted partner in navigating the complexities of the real estate and small business markets. Founded by industry veterans Rafael Moreno and Daniel Oh, we specialize in providing comprehensive services tailored to the unique needs of our clients. Whether you're a franchisee, a new restaurant owner, or a commercial real estate investor, our expertise in due diligence, construction management, and investment property evaluation ensures you make informed, strategic decisions.At Tollbrook Advisory, we are committed to your success. Our approach combines meticulous analysis, strategic insights,</p>
    <a class="btn">Learn more <svg viewBox="0 0 16 16"><circle cx="8" cy="8" r="8" fill="#fff"/><path d="M6 4l4 4-4 4" stroke="#8dc4a7" stroke-width="2" fill="none"/></svg></a>
  </div>
</section>

<section class="team">
  <h2>Our Team</h2>
  <article class="team-card" style="left:109px">
    <div class="member"><div class="avatar" role="img" aria-label="Portrait of Daniel Oh"></div><div><h3>Daniel Oh</h3><span>Principal</span></div></div>
    <p>Daniel Oh is a seasoned real estate expert with extensive experience in project and construction management, and a licensed real estate agent in California. Fluent in both English and Korean, he specializes in commercial real estate, bringing invaluable expertise to Tollbrook Advisory. <a>Read More</a></p>
  </article>
  <article class="team-card" style="left:613px">
    <div class="member"><div class="avatar" role="img" aria-label="Portrait of Rafael Moreno"></div><div><h3>Rafael Moreno</h3><span>Principal</span></div></div>
    <p>Rafael Moreno brings almost 20 years of rich experience as a real estate investor and a pivotal role at one of southern California's largest real estate management firms, where he led sales and marketing strategies to elevate property value and investor returns. His vast expertise spans . <a>Read More</a></p>
  </article>
</section>

<footer class="site-footer">
  <h4 style="left:103px;top:74px">Get in touch</h4>
  <div class="field" style="left:103px;top:122px;width:236px;height:40px">First Name</div>
  <div class="field" style="left:346px;top:122px;width:234px;height:40px">Last Name</div>
  <div class="field" style="left:103px;top:171px;width:236px;height:40px">Email</div>
  <div class="field" style="left:346px;top:171px;width:234px;height:40px">Phone number</div>
  <div class="field" style="left:103px;top:218px;width:477px;height:76px">Message</div>
  <a class="btn" style="position:absolute;left:111px;top:324px;height:40px">Submit now</a>

  <h4 style="left:633px;top:74px">Quick links</h4>
  <ul class="quick"><li>Home</li><li>About Us</li><li>Team</li><li>Services</li><li>Contact</li></ul>

  <h4 style="left:864px;top:74px">Contact us</h4>
  <ul class="contact">
    <li><svg viewBox="0 0 16 16"><path d="M8 1a5 5 0 0 0-5 5c0 4 5 9 5 9s5-5 5-9a5 5 0 0 0-5-5z" fill="#fff"/><circle cx="8" cy="6" r="2" fill="#1c3b2b"/></svg><span>218 Harbor Park Way, Irvine,<br>CA 92614</span></li>
    <li><svg viewBox="0 0 16 16"><rect x="4" y="1" width="8" height="14" rx="1.5" fill="#fff"/><rect x="5.5" y="3" width="5" height="8" fill="#1c3b2b"/></svg><span>+1 555-010-2040</span></li>
    <li><svg viewBox="0 0 16 16"><rect x="1" y="5" width="14" height="9" rx="1" fill="#fff"/><rect x="4" y="1" width="8" height="5" fill="#fff"/></svg><span>555 010 7788</span></li>
    <li><svg viewBox="0 0 16 16"><rect x="1" y="3" width="14" height="10" fill="none" stroke="#fff" stroke-width="1.5"/><path d="M1 3l7 6 7-6" stroke="#fff" stroke-width="1.5" fill="none"/></svg><span>info@tollbrookadvisory.example</span></li>
  </ul>

  <h4 style="left:633px;top:296px">Stay connected :</h4>
  <div class="socials"><span aria-label="Social profile"></span><span aria-label="Social profile"></span><span aria-label="Social profile"></span></div>

  <div class="footer-bottom">© 2024 Tollbrook Advisory &nbsp;| &nbsp; All Rights Reserved &nbsp; | &nbsp; Terms and Conditions</div>
</footer>

</body>
</html>
```